Capability Statement Brochure For Construction Company

Use the current branding/graphics/logo from www.ravelbuildworks.com

The brochure should create the perception that Ravel Buildworks are a big national construction company

View attached PDF for the style and size that we want - Content and images are attached in word docs and provide a road map for this brochure. You can use attached images where you see fit.

The brochure needs to be flawless!

Cover page and one content page is fine for first round elimination
Updates

View attached PDF for style and size references.

Target Market(s)

Business to Business

Industry/Entity Type

Construction

```html
<!DOCTYPE html>
<html lang="en">
<head>
<meta charset="utf-8">
<title>Capability Statement – Corporate Profile</title>
<link href="https://fonts.googleapis.com/css2?family=Didact+Gothic&family=Questrial&display=swap" rel="stylesheet">
<style>
  :root {
    --page: #ffffff;
    --band: #eef1f6;
    --panel: #cdd4df;
    --title-box: #eef1f6;
    --title: #8c97a8;
    --ink: #1c1c1c;
    --header: #5c6470;
    --accent: #1aa552;
  }
  * { box-sizing: border-box; margin: 0; padding: 0; }
  html, body { width: 1200px; height: 849px; overflow: hidden; background: var(--page); }
  .page {
    position: relative;
    width: 1200px;
    height: 849px;
    overflow: hidden;
    background: var(--page);
    font-family: "Didact Gothic", "Century Gothic", sans-serif;
    color: var(--ink);
  }
  .running-header {
    position: absolute;
    left: 777px;
    top: 29px;
    font-family: "Questrial", sans-serif;
    font-size: 13px;
    letter-spacing: 0.3px;
    color: var(--header);
  }
  .band {
    position: absolute;
    left: 0;
    top: 188px;
    width: 1200px;
    height: 567px;
    background: var(--band);
  }
  .title-box {
    position: absolute;
    left: 133px;
    top: 131px;
    width: 524px;
    height: 57px;
    background: var(--title-box);
  }
  .panel {
    position: absolute;
    left: 133px;
    top: 188px;
    width: 800px;
    height: 567px;
    background: var(--panel);
  }
  .section-title {
    position: absolute;
    left: 133px;
    top: 128px;
    font-family: "Questrial", sans-serif;
    font-weight: 700;
    font-size: 21px;
    letter-spacing: 0.2px;
    color: var(--title);
  }
  .intro {
    position: absolute;
    left: 133px;
    top: 186px;
    width: 800px;
    font-size: 12px;
    line-height: 17.2px;
    text-align: justify;
  }
  .sectors {
    position: absolute;
    left: 133px;
    top: 325px;
    list-style: none;
    font-size: 12px;
    line-height: 17.2px;
    color: var(--accent);
  }
  .sectors li { position: relative; padding-left: 27px; }
  .sectors li::before {
    content: "•";
    position: absolute;
    left: 0;
    color: var(--accent);
  }
  .approach {
    position: absolute;
    left: 133px;
    top: 533px;
    width: 526px;
    font-size: 12px;
    line-height: 17.2px;
    text-align: justify;
  }
  .feature-photo {
    position: absolute;
    left: 686px;
    top: 446px;
    width: 514px;
    height: 403px;
    background:
      linear-gradient(180deg, #8a6a4a 0%, #6b3a22 38%, #a05a2e 62%, #d8d2c8 78%, #8b3c1d 100%);
  }
</style>
</head>
<body>
<div class="page">
  <div class="running-header">CAPABILITY STATEMENT</div>

  <div class="band"></div>
  <div class="title-box"></div>
  <div class="panel"></div>

  <h1 class="section-title">CORPORATE PROFILE</h1>

  <p class="intro">Australian Ravel Buildworks (ARB) is an industry leader in the DESIGN AND CONSTRUCT of quality, sustainable living systems and work places for Western Australia.&nbsp; Our expertise lies in delivering building solutions to regional and remote areas. Since 1985, our dynamic team has been partnering with local trade partners who best understand the North West’s challenging operating environment. Together, with our combined local knowledge and expertise, we have created an enviable reputation for creating cutting-edge, cost-efficient, quality-driven, regionally responsive architectures for both the private sector and government. Over the last 30 years we have developed an impressive portfolio of projects across the following sectors:</p>

  <ul class="sectors">
    <li>COMMERCIAL</li>
    <li>CIVIL – ESTATE DEVELOPMENT</li>
    <li>TOURISM</li>
    <li>INDUSTRIAL</li>
    <li>LARGE DEVELOPMENTS FOR GOVERNMENT HOUSING</li>
    <li>RESIDENTIAL HOUSING</li>
    <li>REFURBISHMENT/FITOUT</li>
    <li>RETAIL SHOPS</li>
    <li>RESORTS</li>
    <li>MINING / WORKERS’CAMPS</li>
    <li>REMOTE FLIGHT STRIPS</li>
  </ul>

  <p class="approach">We embrace the client as a partner in every building project. Working together, we seek to evolve the most cost-effective building solution, tailored to each client’s needs, budget and time frame without compromising on quality.&nbsp; We make it a joint journey because like any “joint venture”, collaboration is the key to a successful outcome.</p>

  <div class="feature-photo" role="img" aria-label="Photograph of a modern reception lobby with timber wall panels, white banded reception counters and a polished timber floor"></div>
</div>
</body>
</html>
```